Application page web design and internal pages

Create a web site where home
Page looks like an application screen for a mobile phone

Use bold icons and colors with images that have round edges

PorlenPurse Apps is name of page

Search bar at the top

Use colors from Vextaro.org for background

Price of ZORBS in top right corner (https://www.quelvix.example/trade/en-US?symbol=ZORBS_USDT&layout=basic&theme=dark)

Pages within each app should be the same color as the icon

Use the following as app icons on the page:
Key
Icon name: first screen; second screen (text)

⁃ Balances: enter pin; display balances (Your account can hold multiple currency denominations. Your balances are: ZORBS 1234567890)
⁃ Transactions: enter pin; display transactions (Your last 5 payments are ZORBS 10 from Vextaro)
⁃ Send Money: enter phone number, enter amount, send button; display message
⁃ Create Account: choose country code, enter phone number, create button; enter pin; display message ( (phone number) will be notified when their account has been created)
⁃ My Wallet Address: enter pin; display public key (IMPORTANT Send only STELLAR blockchain tokens to this deposit address: GDXQ7PLM2ZNVA9TRK4WSEY8HCBUJ6FOGDLIXP3QM5RTVKNAWZEHOBCYS)
⁃ Private Message: enter phone number, enter message, choose image, send button; enter pin; display message ( (phone number) will be notified when their message has been created)
⁃ Buy Cryptocurrency: drop drown menu of cryptocurrency to purchase (Bitcoin/Ethereum/Stellar/ZORBS), Amount in USD field, amount in chosen cryptocurrency displayed, frequency drop down menu (once/daily/weekly/monthly), buy button; enter card information (name, card number, expiration date, cvv, billing address, zip code), confirm buy button, transactions will appear on your billing statement as VEXTARO; enter pin screen; display message (You will be notified when your coin is received)
⁃ NFTs: upload image, title, description, link media, create NFT button; enter pin screen; display message (You will be notified when your NFT is created)
⁃ Earn: display message (Earn cryptocurrency doing what you do everyday, coming soon)
⁃ Files/Vault: display message (Storage for your photos, documents and more, coming soon)
⁃ Wealth: display message (Build wealth by working with a financial professional to get you to the next level), check box (I would like a financial professional to contact me about building wealth), contact me button; display message (A financial professional will contact you to achieve your financial goals)
⁃ Education: display message (Learn more about everything, coming soon)
⁃ News: display message (News from around the world, coming soon)
⁃ FAQs: use FAQs from this link https://vextaro.example/faq
⁃ Contact Us: enter message, send button; display message (Thank you for reaching out. We will reply to your message in the order it was received. Your patience is appreciated. Blessings.)

Requirements
Must have
• Application home page that looks like the Home Screen of a mobile phone
Nice to have
• Colorful icons

```html
<!DOCTYPE html>
<html lang="en">
<head>
<meta charset="utf-8">
<title>PorlenPurse Apps – Balances &amp; Transactions</title>
<link href="https://fonts.googleapis.com/css2?family=Roboto:wght@400;500;700;900&family=Poppins:wght@400;500&display=swap" rel="stylesheet">
<style>
:root{
  --board:#bfc0c2;
  --ink:#0b0b0f;
  --navy:#14143a;
  --navy-deep:#0e1f45;
  --ocean:#14476e;
  --teal:#23b0c6;
  --teal-text:#1ba9c4;
  --white:#ffffff;
  --muted:#5d5d66;
  --line:#b9b9c0;
}
*{box-sizing:border-box;margin:0;padding:0}
html,body{width:1200px;height:1134px;overflow:hidden}
body{background:var(--board);font-family:"Roboto",Arial,sans-serif;color:var(--ink);position:relative}
.section-title{position:absolute;left:118px;font-weight:900;font-size:34px;letter-spacing:-0.3px;line-height:1}
.section-title.balances{top:62px}
.section-title.transactions{top:576px}

.screen{position:absolute;overflow:hidden;background:var(--white);--pad:20px;--menu:18px}
.screen.phone{width:177px;height:388px;--pad:9px;--menu:7px}
.screen.flat{width:201px;height:388px}
.hero{position:absolute;left:0;top:0;width:100%;height:388px}
.brand{position:absolute;left:0;right:0;top:38px;text-align:center;color:var(--white)}
.brand-mark{display:block;width:10px;height:10px;border:1.2px solid var(--white);border-radius:2px;margin:0 auto 9px}
.brand-name{font-weight:500;font-size:9.5px;letter-spacing:1.6px}
.price-bar{position:absolute;top:81px;left:50%;width:117px;height:29px;margin-left:-58px;background:var(--navy);border-radius:2px;color:var(--white);font-size:7.5px;display:flex;align-items:center;justify-content:space-between;padding:0 11px;box-shadow:0 2px 5px rgba(0,0,0,.25)}
.price-bar .coin::after{content:"⌄";font-size:6px;margin-left:4px;position:relative;top:-1px}
.price-bar .rate::after{content:"↑";font-size:6.5px;margin-left:5px}
.search{position:absolute;top:124px;left:var(--pad);right:var(--pad);height:21px;background:var(--white);box-shadow:0 1px 5px rgba(0,0,0,.16);border-radius:2px;display:flex;align-items:center;justify-content:space-between;padding-left:7px}
.search-hint{font-family:"Poppins",Arial,sans-serif;font-size:5px;color:#55555e}
.search-btn{width:19px;height:19px;background:var(--navy);border-radius:2px;margin-right:1px;display:flex;align-items:center;justify-content:center}
.menu-toggle{position:absolute;top:170px;left:var(--menu);width:14px;height:10px}
.pin-panel{position:absolute;top:192px;left:0;right:0;text-align:center}
.pin-title{font-weight:500;font-size:9px;letter-spacing:.2px}
.pin-hint{font-size:7px;color:var(--muted);margin-top:11px}
.pin-slots{display:flex;justify-content:center;gap:16px;margin-top:21px}
.pin-slots span{width:19px;border-bottom:1px solid var(--line)}
.send-btn{display:inline-block;margin-top:18px;width:72px;height:19px;line-height:19px;border-radius:10px;background:var(--navy);color:var(--white);font-weight:500;font-size:7.5px}
.balance-panel{position:absolute;top:189px;left:0;right:0;text-align:center;font-size:7px;color:#3b3b44}
.balance-panel p+p{margin-top:11px;font-size:7.5px}
.balance-panel b{font-weight:700;font-size:8.5px;color:var(--ink)}
.policy{position:absolute;bottom:26px;left:0;right:0;text-align:center;font-size:4px;color:#3b3b44}
.home-bar{position:absolute;left:0;right:0;bottom:0;height:20px;background:var(--navy);display:flex;align-items:center;justify-content:center}

.dim{position:absolute;inset:0;background:rgba(28,28,36,.66)}
.drawer{position:absolute;left:0;top:175px;bottom:0;width:100px;background:var(--navy);border-top-right-radius:5px;padding-top:9px}
.drawer li{list-style:none;display:flex;align-items:center;height:19.8px;padding-left:18px;color:var(--white);font-size:5.4px;font-weight:500}
.drawer .app-icon{width:12px;height:12px;border-radius:2px;margin-right:7px;background:var(--white);display:flex;align-items:center;justify-content:center}
.drawer .app-icon i{display:block;width:7px;height:7px;border-radius:50%}

.tx-head{position:absolute;top:186px;left:24px;right:23px;display:flex;justify-content:space-between;align-items:center}
.tx-head h3{font-size:8px;font-weight:700;letter-spacing:.2px}
.sort{font-size:5.5px;color:var(--muted)}
.sort b{color:var(--ink);font-size:6.5px;margin-left:3px}
.sort b::after{content:"⌄";font-size:5px;margin-left:2px}
.tx-day{position:absolute;left:24px;font-size:5.8px;font-weight:500;color:#3b3b44;text-decoration:underline}
.tx{position:absolute;left:24px;right:23px;display:flex;justify-content:space-between}
.tx-name{font-size:7.5px;font-weight:500;color:var(--ink)}
.tx-time{font-size:4.6px;color:#3b3b44;margin-top:4px}
.tx-amt{font-size:5.6px;font-weight:500;margin-top:4px}
.tx-amt.in{color:var(--teal-text)}
.tx-amt.out{color:var(--ink)}
</style>
</head>
<body>

<svg width="0" height="0" style="position:absolute" aria-hidden="true">
  <defs>
    <linearGradient id="heroFill" x1="0" y1="0" x2="1" y2="1">
      <stop offset="0" stop-color="#0e1f45"/>
      <stop offset=".55" stop-color="#14476e"/>
      <stop offset="1" stop-color="#23b0c6"/>
    </linearGradient>
    <symbol id="heroShape" viewBox="0 0 201 388" preserveAspectRatio="none">
      <path d="M12 0H201V162C190 132 168 116 128 102C72 86 30 62 12 0Z" fill="url(#heroFill)"/>
    </symbol>
    <symbol id="loupe" viewBox="0 0 12 12"><circle cx="5" cy="5" r="3.8" fill="none" stroke="#fff" stroke-width="1"/><path d="M7.8 7.8L11 11" stroke="#fff" stroke-width="1" stroke-linecap="round"/></symbol>
    <symbol id="bars" viewBox="0 0 14 10"><path d="M0 1H14M0 5H14M0 9H14" stroke="#14143a" stroke-width="1.6"/></symbol>
    <symbol id="house" viewBox="0 0 10 10"><path d="M5 .8L.5 5H2v4h2.3V6.4h1.4V9H8V5h1.5Z" fill="#fff"/></symbol>
  </defs>
</svg>

<h1 class="section-title balances">BALANCES</h1>

<!-- Balances: enter pin -->
<section class="screen phone" style="left:131px;top:134px">
  <svg class="hero"><use href="#heroShape"/></svg>
  <div class="brand"><span class="brand-mark"></span><span class="brand-name">PORLENPURSE</span></div>
  <div class="price-bar"><span class="coin">ZORBS</span><span class="rate">$ 5.98</span></div>
  <div class="search"><span class="search-hint">Search Here</span><span class="search-btn"><svg width="11" height="11"><use href="#loupe"/></svg></span></div>
  <svg class="menu-toggle"><use href="#bars"/></svg>
  <div class="pin-panel">
    <h2 class="pin-title">BALANCES</h2>
    <p class="pin-hint">Enter Your Pin Here</p>
    <div class="pin-slots"><span></span><span></span><span></span><span></span></div>
    <span class="send-btn">SEND</span>
  </div>
  <p class="policy">©Vextaro Zero Liability Transaction Policy</p>
  <div class="home-bar"><svg width="9" height="9"><use href="#house"/></svg></div>
</section>

<!-- Balances: display -->
<section class="screen flat" style="left:381px;top:134px">
  <svg class="hero"><use href="#heroShape"/></svg>
  <div class="brand"><span class="brand-mark"></span><span class="brand-name">PORLENPURSE</span></div>
  <div class="price-bar"><span class="coin">ZORBS</span><span class="rate">$ 5.98</span></div>
  <div class="search"><span class="search-hint">Search Here</span><span class="search-btn"><svg width="11" height="11"><use href="#loupe"/></svg></span></div>
  <svg class="menu-toggle"><use href="#bars"/></svg>
  <div class="balance-panel">
    <p>Your balances are:</p>
    <p>ZORBS <b>1234567890</b></p>
  </div>
  <p class="policy">©Vextaro Zero Liability Transaction Policy</p>
  <div class="home-bar"><svg width="9" height="9"><use href="#house"/></svg></div>
</section>

<!-- Balances: menu open -->
<section class="screen flat" style="left:640px;top:132px;height:392px">
  <svg class="hero"><use href="#heroShape"/></svg>
  <div class="brand"><span class="brand-mark"></span><span class="brand-name">PORLENPURSE</span></div>
  <div class="price-bar"><span class="coin">ZORBS</span><span class="rate">$ 5.98</span></div>
  <div class="search"><span class="search-hint">Search Here</span><span class="search-btn"><svg width="11" height="11"><use href="#loupe"/></svg></span></div>
  <div class="pin-panel" style="top:180px">
    <h2 class="pin-title">BALANCES</h2>
    <p class="pin-hint">Enter Your Pin Here</p>
    <div class="pin-slots"><span></span><span></span><span></span><span></span></div>
    <span class="send-btn">SEND</span>
  </div>
  <div class="dim"></div>
  <svg class="menu-toggle" style="opacity:.9"><use href="#bars"/></svg>
  <ul class="drawer">
    <li><span class="app-icon"><i role="img" aria-label="Balances app icon" style="background:#e58a2c"></i></span>Balances</li>
    <li><span class="app-icon"><i role="img" aria-label="Transactions app icon" style="background:#7fc4e8"></i></span>Transactions</li>
    <li><span class="app-icon"><i role="img" aria-label="Send Money app icon" style="background:#e8c23a"></i></span>Send Money</li>
    <li><span class="app-icon"><i role="img" aria-label="Create Account app icon" style="background:#f3a74a"></i></span>Create Account</li>
    <li><span class="app-icon"><i role="img" aria-label="Wallet Address app icon" style="background:#d9534a"></i></span>Wallet Address</li>
    <li><span class="app-icon"><i role="img" aria-label="Private Message app icon" style="background:#e2463f"></i></span>Private Message</li>
    <li><span class="app-icon"><i role="img" aria-label="Buy Cryptocurrency app icon" style="background:#3d8fd8"></i></span>Buy Cryptocurrency</li>
    <li><span class="app-icon"><i role="img" aria-label="NFTs app icon" style="background:#8a5a30"></i></span>NFTs</li>
    <li><span class="app-icon"><i role="img" aria-label="Earn app icon" style="background:#e39a3b"></i></span>Earn</li>
    <li><span class="app-icon"><i role="img" aria-label="Files and Vault app icon" style="background:#3a6fd8"></i></span>Files/Vault</li>
    <li><span class="app-icon"><i role="img" aria-label="Wealth app icon" style="background:#4ea86a"></i></span>Wealth</li>
  </ul>
</section>

<h1 class="section-title transactions">TRANSACTIONS</h1>

<!-- Transactions: enter pin -->
<section class="screen phone" style="left:131px;top:645px">
  <svg class="hero"><use href="#heroShape"/></svg>
  <div class="brand"><span class="brand-mark"></span><span class="brand-name">PORLENPURSE</span></div>
  <div class="price-bar"><span class="coin">ZORBS</span><span class="rate">$ 5.98</span></div>
  <div class="search"><span class="search-hint">Search Here</span><span class="search-btn"><svg width="11" height="11"><use href="#loupe"/></svg></span></div>
  <svg class="menu-toggle"><use href="#bars"/></svg>
  <div class="pin-panel">
    <h2 class="pin-title">TRANSACTIONS</h2>
    <p class="pin-hint">Enter Your Pin Here</p>
    <div class="pin-slots"><span></span><span></span><span></span><span></span></div>
    <span class="send-btn">SEND</span>
  </div>
  <p class="policy">©Vextaro Zero Liability Transaction Policy</p>
  <div class="home-bar"><svg width="9" height="9"><use href="#house"/></svg></div>
</section>

<!-- Transactions: list -->
<section class="screen flat" style="left:379px;top:642px;width:203px;height:393px">
  <svg class="hero"><use href="#heroShape"/></svg>
  <div class="brand"><span class="brand-mark"></span><span class="brand-name">PORLENPURSE</span></div>
  <div class="price-bar"><span class="coin">ZORBS</span><span class="rate">$ 5.98</span></div>
  <div class="search"><span class="search-hint">Search Here</span><span class="search-btn"><svg width="11" height="11"><use href="#loupe"/></svg></span></div>
  <svg class="menu-toggle"><use href="#bars"/></svg>
  <div class="tx-head"><h3>TRANSACTIONS</h3><span class="sort">Sort By<b>Date</b></span></div>
  <p class="tx-day" style="top:206px">Today</p>
  <div class="tx" style="top:221px"><div><p class="tx-name">Lorem Ipsum Is Dummy</p><p class="tx-time">Just Now</p></div><p class="tx-amt in">+ 50.00 $</p></div>
  <div class="tx" style="top:246px"><div><p class="tx-name">Lorem Ipsum Is Dummy</p><p class="tx-time">10.45 AM</p></div><p class="tx-amt out">- 30.00 $</p></div>
  <p class="tx-day" style="top:275px">08 March 2023</p>
  <div class="tx" style="top:289px"><div><p class="tx-name">Lorem Ipsum Is Dummy</p><p class="tx-time">09.10 AM</p></div><p class="tx-amt in">+ 50.00 $</p></div>
  <div class="tx" style="top:315px"><div><p class="tx-name">Lorem Ipsum Is Dummy</p><p class="tx-time">10.45 AM</p></div><p class="tx-amt out">- 30.00 $</p></div>
  <div class="tx" style="top:341px"><div><p class="tx-name">Lorem Ipsum Is Dummy</p><p class="tx-time">19.45 PM</p></div><p class="tx-amt in">+30.00 $</p></div>
  <p class="policy" style="bottom:27px">©Vextaro Zero Liability Transaction Policy</p>
  <div class="home-bar"><svg width="9" height="9"><use href="#house"/></svg></div>
</section>

</body>
</html>
```